Banner poster with different motifs

I'm looking for 5 banners and posters in A1 format in the same design, or the similarity must be recognizable...
Kept quite simple with different titles.

1 ballet
2 Contemporary Dance
3 high heels
4 Salsa & Bachata & Zouk
5 Hip Hop

Modern bright colors
it is for the entrance so that the students see here is a dance school

The text may also be included in the image
The photos are for guidance only; some are our own, some are purchased. However, we are permitted to use them, including our logo, of course.

```html
<!DOCTYPE html>
<html lang="en">
<head>
<meta charset="utf-8">
<title>Ballet – Dance Poster</title>
<link rel="stylesheet" href="https://fonts.googleapis.com/css2?family=Poppins:wght@300;400;600&display=swap">
<style>
  :root {
    --stage-bg: #efeded;
    --pink-light: #fde8f4;
    --pink-mid: #fcc6e8;
    --pink-edge: #fba6dc;
    --plum: #8a0a55;
    --ink: #2a1420;
    --ring: rgba(255, 255, 255, 0.55);
    --photo-core: rgba(150, 112, 122, 0.30);
    --photo-fade: rgba(150, 112, 122, 0);
  }
  html, body {
    margin: 0;
    width: 938px;
    height: 1200px;
    overflow: hidden;
    background: var(--stage-bg);
  }
  .poster {
    position: absolute;
    left: 45px;
    top: 0;
    width: 848px;
    height: 1200px;
  }
  .poster svg { display: block; }
  .title-letter {
    font-family: "Poppins", sans-serif;
    font-weight: 600;
    font-size: 160px;
    fill: var(--plum);
  }
  .brand-name {
    font-family: "Poppins", sans-serif;
    font-weight: 300;
    font-size: 36px;
    fill: var(--ink);
  }
  .brand-tagline {
    font-family: "Poppins", sans-serif;
    font-weight: 300;
    font-size: 11px;
    fill: var(--ink);
  }
  .web-address {
    font-family: "Poppins", sans-serif;
    font-weight: 400;
    font-size: 30px;
    fill: var(--ink);
  }
</style>
</head>
<body>
<div class="poster">
  <svg width="848" height="1200" viewBox="0 0 848 1200" xmlns="http://www.w3.org/2000/svg">
    <defs>
      <radialGradient id="backdrop" cx="0.55" cy="0.55" r="0.75">
        <stop offset="0" stop-color="var(--pink-light)"/>
        <stop offset="0.6" stop-color="var(--pink-mid)"/>
        <stop offset="1" stop-color="var(--pink-edge)"/>
      </radialGradient>
      <radialGradient id="photo-tone" cx="0.5" cy="0.5" r="0.5">
        <stop offset="0" stop-color="var(--photo-core)"/>
        <stop offset="0.7" stop-color="var(--photo-core)"/>
        <stop offset="1" stop-color="var(--photo-fade)"/>
      </radialGradient>
    </defs>

    <rect class="backdrop" width="848" height="1200" fill="url(#backdrop)"/>

    <g class="rings" fill="none" stroke="var(--ring)" stroke-width="1.5">
      <circle cx="424" cy="708" r="330"/>
      <circle cx="424" cy="708" r="275"/>
      <circle cx="424" cy="708" r="220"/>
      <circle cx="424" cy="708" r="165"/>
    </g>

    <rect class="dancer-photo" role="img"
      aria-label="Photo of a ballet dancer in a pale pink and mauve leotard leaping in a split jump with motion trails"
      x="25" y="250" width="760" height="870" fill="url(#photo-tone)"/>

    <g class="title-ballet">
      <text class="title-letter" x="254" y="293">B</text>
      <text class="title-letter" x="393" y="376">A</text>
      <text class="title-letter" x="292" y="605">L</text>
      <text class="title-letter" x="477" y="697">L</text>
      <text class="title-letter" x="502" y="936">E</text>
      <text class="title-letter" x="668" y="1035">T</text>
    </g>

    <g class="brand">
      <circle cx="675" cy="101" r="42" fill="none" stroke="var(--ink)" stroke-width="1.5"/>
      <text class="brand-name" x="542" y="187" textLength="235" lengthAdjust="spacingAndGlyphs">MOVIDANZA</text>
      <text class="brand-tagline" x="542" y="205" textLength="235" lengthAdjust="spacing">DANCE CENTER FRANKFURT</text>
    </g>

    <text class="web-address" x="97" y="1113" textLength="363" lengthAdjust="spacing">www.movidanza.de</text>
  </svg>
</div>
</body>
</html>
```